Verodex business card

Business card for sustainable investment company called "Verodex". Verodex is an exchange platform selling carbon credits between buyers and sellers. Carbon Credits are an environmental commodity for reducing global carbon emissions.

the card should obviously have our logo and the theme should be sustainability/environment mixed with a trading platform.

Contact Information for Business Card

Logo, Name, Title, Phone, Email

Colors
0054AA
0677BA
7BADD7
CADEEF
E8F1F8
0094D4
00A9DD
6FCCEA
C7EBF8
E9F6FB
00AB8E
00BBA5
67D7C9
C6EFE9
E9F9F6
59FF00
82FF00
B8FF75
E3FFCB
F4FFEA

```html
<!DOCTYPE html>
<html lang="en">
<head>
<meta charset="utf-8">
<title>Verodex business card</title>
<link href="https://fonts.googleapis.com/css2?family=Montserrat:wght@400;500;600;700&display=swap" rel="stylesheet">
<style>
  :root {
    --navy: #16294f;
    --white: #ffffff;
    --page: #eceef0;
    --blue: #4a78c4;
    --sky: #2fbfe9;
    --aqua: #6fcfe0;
  }
  * { margin: 0; padding: 0; box-sizing: border-box; }
  html, body { width: 1200px; height: 900px; overflow: hidden; }
  body {
    background: var(--page);
    font-family: "Montserrat", sans-serif;
    display: flex;
    flex-direction: column;
    align-items: center;
    justify-content: center;
    gap: 40px;
  }
  .card {
    position: relative;
    width: 700px;
    height: 400px;
    overflow: hidden;
    box-shadow: 0 6px 18px rgba(0,0,0,0.12);
  }
  .card--front {
    background: var(--navy);
    display: flex;
    align-items: center;
    justify-content: center;
  }
  .brand {
    display: flex;
    align-items: center;
    gap: 22px;
  }
  .brand__dot {
    width: 64px;
    height: 64px;
    border-radius: 50%;
    background: var(--sky);
  }
  .brand__name {
    font-weight: 600;
    font-size: 72px;
    letter-spacing: 2px;
    color: var(--white);
    text-transform: uppercase;
  }
  .card--back { background: var(--white); }
  .card__wave { position: absolute; inset: 0; }
  .card--back .brand {
    position: absolute;
    left: 60px;
    top: 118px;
    gap: 14px;
  }
  .card--back .brand__dot { width: 40px; height: 40px; }
  .card--back .brand__name { font-size: 44px; color: var(--navy); letter-spacing: 1px; }
  .contact {
    position: absolute;
    right: 28px;
    top: 150px;
    text-align: right;
    color: var(--white);
  }
  .contact__name {
    font-weight: 700;
    font-size: 21px;
    letter-spacing: 1px;
    text-transform: uppercase;
    white-space: nowrap;
  }
  .contact__title {
    font-weight: 400;
    font-size: 15px;
    margin-top: 2px;
  }
  .contact__list {
    list-style: none;
    margin-top: 22px;
    font-size: 15px;
    line-height: 28px;
  }
  .contact__list li {
    display: flex;
    justify-content: flex-end;
    align-items: center;
    gap: 12px;
    white-space: nowrap;
  }
  .contact__icon { width: 15px; height: 15px; fill: var(--white); }
</style>
</head>
<body>

  <section class="card card--front">
    <div class="brand">
      <span class="brand__dot"></span>
      <span class="brand__name">Verodex</span>
    </div>
  </section>

  <section class="card card--back">
    <svg class="card__wave" viewBox="0 0 700 400" preserveAspectRatio="none">
      <defs>
        <linearGradient id="waveGradient" x1="0" y1="1" x2="1" y2="0">
          <stop offset="0" stop-color="#6fcfe0"/>
          <stop offset="0.5" stop-color="#2fbfe9"/>
          <stop offset="1" stop-color="#4a78c4"/>
        </linearGradient>
      </defs>
      <path d="M 604 0 C 490 40, 440 180, 400 262 C 352 350, 272 388, 150 400 L 700 400 L 700 0 Z" fill="url(#waveGradient)"/>
      <path d="M 634 0 C 520 40, 470 180, 430 262 C 382 350, 302 390, 182 400 L 700 400 L 700 0 Z" fill="#16294f"/>
    </svg>

    <div class="brand">
      <span class="brand__dot"></span>
      <span class="brand__name">Verodex</span>
    </div>

    <div class="contact">
      <p class="contact__name">Daniel Marsh</p>
      <p class="contact__title">Co-Founder</p>
      <ul class="contact__list">
        <li>555-014-2290
          <svg class="contact__icon" viewBox="0 0 16 16"><path d="M3 1h3l1.5 4-2 1.2a9 9 0 0 0 4.3 4.3L11 8.5l4 1.5v3a2 2 0 0 1-2 2A12 12 0 0 1 1 3a2 2 0 0 1 2-2z"/></svg>
        </li>
        <li>info@verodex.com
          <svg class="contact__icon" viewBox="0 0 16 16"><path d="M1 3h14v10H1z M2 4.2v.4l6 4 6-4v-.4z" fill-rule="evenodd"/></svg>
        </li>
        <li>www.verodex.com
          <svg class="contact__icon" viewBox="0 0 16 16"><circle cx="8" cy="8" r="7"/><path d="M1 8h14M8 1c3 3 3 11 0 14M8 1c-3 3-3 11 0 14" stroke="#16294f" stroke-width="1" fill="none"/></svg>
        </li>
      </ul>
    </div>
  </section>

</body>
</html>
```